Tidewell Comforts, a portable luxury restroom trailer company needs a landing page

We need a landing page for a luxury portable restroom trailer company. This should be modern, and simple - use any combination of Pantone colors: Warm Gray 1C, Black 7C, 7529c, 873C, 8003C

We rent these trailers for special events like weddings, private parties, festivals, family reunions, team building, wine tastings, beer tastings, food truck round-ups, etc.

An idea of the landing page is in the files below. Please use stock photography and placeholder text for now. The winning design will be given final content.

Requirements
Must have
• Multiple "Get Quote" buttons or a place for them to type in type of rental, how many people etc

```html
<!DOCTYPE html>
<html lang="en">
<head>
<meta charset="utf-8">
<title>Tidewell Comforts</title>
<link href="https://fonts.googleapis.com/css2?family=Roboto+Slab:wght@300;400;500;600&family=Roboto:wght@400;500&display=swap" rel="stylesheet">
<style>
:root{
  --black7:#3d3935;
  --black-deep:#2a2724;
  --gold873:#85714d;
  --gold8003:#8c7a57;
  --stone7529:#b7ada2;
  --warmgray1:#d7d2cb;
  --warmgray-bg:#efece8;
  --ink:#2e2b28;
  --text:#5a5550;
  --line:#cfc9c1;
  --white:#fff;
}
*{margin:0;padding:0;box-sizing:border-box}
html,body{width:1200px;height:2948px;overflow:hidden;background:var(--white)}
body{position:relative;font-family:"Roboto Slab",serif;color:var(--ink)}
.abs{position:absolute}

/* header */
.top-band{left:0;top:0;width:1200px;height:423px;overflow:hidden;
  background:radial-gradient(ellipse at 88% 85%,rgba(140,122,87,.55) 0%,transparent 45%),
  linear-gradient(160deg,var(--black7) 0%,var(--black-deep) 55%,#4a433b 100%)}
.top-band::before{content:"";position:absolute;left:-120px;top:290px;width:300px;height:160px;
  border-radius:50%;background:rgba(0,0,0,.25);transform:rotate(25deg)}
.brand{left:112px;top:38px;font-size:30px;font-weight:600;color:var(--white);white-space:nowrap}
.nav a{position:absolute;color:var(--white);text-decoration:none;font-size:15px;letter-spacing:.3px;top:51px;white-space:nowrap}
.nav .active{border:1px solid var(--white);border-radius:18px;padding:7px 17px;top:43px}

/* hero collage */
.hero{left:112px;top:118px;width:977px;height:563px;background:var(--white);
  box-shadow:0 2px 6px rgba(0,0,0,.15)}
.hero-shadow{left:200px;top:680px;width:800px;height:26px;border-radius:50%;
  background:radial-gradient(ellipse at center,rgba(0,0,0,.55) 0%,rgba(0,0,0,0) 70%)}
.tile{position:absolute}

.sec-title{width:1200px;text-align:center;font-size:38px;font-weight:500;color:var(--ink)}
.rule{width:48px;height:3px;background:var(--gold873)}

/* events */
.event-img{top:842px;width:317px;height:251px}
.event-card{top:1062px;width:293px;height:265px;background:var(--white);
  box-shadow:0 2px 8px rgba(0,0,0,.12);text-align:center;padding-top:42px}
.event-date{font-size:22px;color:var(--gold873);font-weight:400}
.event-name{font-size:21px;font-weight:500;margin-top:14px;color:var(--ink)}
.event-text{font-size:14px;line-height:26px;color:var(--text);font-weight:300;margin:16px 20px 0}
.arrow{top:1032px}

/* products */
.products-band{left:0;top:1409px;width:1200px;height:639px;background:var(--warmgray-bg)}
.product-card{top:1552px;width:231px;height:410px;background:var(--white);
  box-shadow:0 1px 4px rgba(0,0,0,.12);text-align:center}
.product-img{position:absolute;left:8px;top:11px;width:215px;height:182px}
.product-name{position:absolute;top:212px;width:100%;font-size:21px;font-weight:400}
.product-text{position:absolute;top:254px;left:12px;right:12px;font-family:"Roboto",sans-serif;
  font-size:14px;line-height:24px;color:var(--text)}
.product-btn{position:absolute;top:339px;left:48px;width:135px;height:46px;border:2px solid var(--black7);
  border-radius:24px;font-size:15px;color:var(--black7);line-height:42px}

/* contact */
.contact-photo{left:0;top:2048px;width:600px;height:583px;
  background:linear-gradient(90deg,rgba(255,255,255,0) 70%,#fff 100%),
  linear-gradient(180deg,#e4e1dc 0%,#c9c3ba 40%,#8a8e96 75%,#d9d6d1 100%)}
.quote-title{left:470px;top:2104px;font-size:38px;font-weight:500;white-space:nowrap}
.field{height:45px;border:1px solid var(--line);border-radius:3px;background:var(--white);
  font-size:14px;color:#333;padding:0 13px;line-height:43px;white-space:nowrap}
.field.select::after{content:"";position:absolute;right:18px;top:20px;border:5px solid transparent;border-top-color:#555}
.submit{left:469px;top:2512px;width:180px;height:55px;border-radius:28px;
  background:linear-gradient(180deg,var(--gold8003),var(--black7));color:var(--white);font-size:18px;
  font-weight:500;text-align:center;line-height:55px}

/* footer */
.footer{left:0;top:2631px;width:1200px;height:317px;background:var(--black7);color:var(--white)}
.footer-brand{width:1200px;text-align:center;top:53px;font-size:38px;font-weight:600}
.footer-nav a{position:absolute;top:128px;color:var(--white);font-size:15px;text-decoration:none;transform:translateX(-50%);white-space:nowrap}
.social{position:absolute;top:188px;width:36px;height:36px;border:2px solid var(--white);border-radius:50%;transform:translateX(-50%);
  display:flex;align-items:center;justify-content:center}
.copy{width:1200px;text-align:center;top:247px;font-size:15px}
</style>
</head>
<body>

<header>
  <div class="abs top-band"></div>
  <div class="abs brand">Tidewell Comforts</div>
  <nav class="nav">
    <a class="active" style="left:659px">HOME</a>
    <a style="left:773px">EVENT</a>
    <a style="left:874px">PRODUCT</a>
    <a style="left:995px">CONTACT US</a>
  </nav>
</header>

<div class="abs hero-shadow"></div>
<section class="abs hero">
  <div class="tile" style="left:8px;top:10px;width:264px;height:264px;background:linear-gradient(135deg,#e9eaec,#b9bcc0)" role="img" aria-label="White restroom trailer with workers at the door"></div>
  <div class="tile" style="left:280px;top:10px;width:330px;height:264px;background:linear-gradient(160deg,#f0f1f3,#9fa4a8)" role="img" aria-label="White multi-stall restroom trailer with steps"></div>
  <div class="tile" style="left:618px;top:10px;width:170px;height:187px;background:linear-gradient(160deg,#3a86c9,#c23a3a 60%,#6e9a4a)" role="img" aria-label="Blue and red portable toilet trailer on grass"></div>
  <div class="tile" style="left:796px;top:10px;width:169px;height:264px;background:linear-gradient(160deg,#cfd8e2,#1d5fb8 50%,#6d7a86)" role="img" aria-label="Blue portable toilet unit"></div>
  <div class="tile" style="left:618px;top:206px;width:170px;height:191px;background:linear-gradient(160deg,#3d3a40,#ee6a25 50%,#6c6560)" role="img" aria-label="Orange portable toilet on a trailer"></div>
  <div class="tile" style="left:618px;top:410px;width:170px;height:143px;background:linear-gradient(180deg,#c8dcee,#e0b830 60%,#707070)" role="img" aria-label="Yellow container restroom unit"></div>
  <div class="tile" style="left:8px;top:284px;width:321px;height:269px;background:linear-gradient(160deg,#6a8a5a,#1f5a3a 45%,#555)" role="img" aria-label="Green restroom trailer with separate doors"></div>
  <div class="tile" style="left:335px;top:284px;width:275px;height:269px;background:linear-gradient(160deg,#4f6a3c,#1c5fb0 50%,#7a5a40)" role="img" aria-label="Blue portable toilet in a vineyard"></div>
  <div class="tile" style="left:796px;top:284px;width:169px;height:269px;background:linear-gradient(160deg,#b8c6d4,#e2e4e6 50%,#5a5e62)" role="img" aria-label="White single restroom trailer"></div>
</section>

<h2 class="abs sec-title" style="left:0;top:750px">Latest Events</h2>
<div class="abs rule" style="left:576px;top:807px"></div>

<svg class="abs arrow" style="left:46px" width="26" height="102" viewBox="0 0 26 102"><polyline points="25,1 1,51 25,101" fill="none" stroke="#555" stroke-width="1.5"/></svg>
<svg class="abs arrow" style="left:1128px" width="26" height="102" viewBox="0 0 26 102"><polyline points="1,1 25,51 1,101" fill="none" stroke="#555" stroke-width="1.5"/></svg>

<div class="abs event-img" style="left:111px;background:linear-gradient(180deg,#3a2a1a,#a06a3a 45%,#b8a0c8)" role="img" aria-label="Evening wedding reception tables under string lights"></div>
<div class="abs event-img" style="left:442px;background:linear-gradient(160deg,#2a5a7a,#e8e0d0 50%,#2a3a5a)" role="img" aria-label="Friends celebrating with drinks on a boat"></div>
<div class="abs event-img" style="left:772px;background:linear-gradient(180deg,#6a8a5a,#5a4a3a 50%,#8a6a4a)" role="img" aria-label="Family dinner outdoors in a garden"></div>

<article class="abs event-card" style="left:123px">
  <div class="event-date">31,Jan 2022</div>
  <div class="event-name">Weddings</div>
  <p class="event-text">Nemo enim ipsam voluptatem quia vo luptas sit aspernatur aut odit aut fugit, sed quia consequuntur magni dolores eos qui ratione</p>
</article>
<article class="abs event-card" style="left:454px">
  <div class="event-date">31,Jan 2022</div>
  <div class="event-name">Private Parties</div>
  <p class="event-text">Nemo enim ipsam voluptatem quia vo luptas sit aspernatur aut odit aut fugit, sed quia consequuntur magni dolores eos qui ratione</p>
</article>
<article class="abs event-card" style="left:784px">
  <div class="event-date">31,Jan 2022</div>
  <div class="event-name">Family Reunions</div>
  <p class="event-text">Nemo enim ipsam voluptatem quia vo luptas sit aspernatur aut odit aut fugit, sed quia consequuntur magni dolores eos qui ratione</p>
</article>

<div class="abs products-band"></div>
<h2 class="abs sec-title" style="left:0;top:1453px">Our Products</h2>
<div class="abs rule" style="left:576px;top:1511px"></div>

<article class="abs product-card" style="left:111px">
  <div class="product-img" style="background:linear-gradient(135deg,#4a4540,#d8d8d8 55%,#8a8a8a)" role="img" aria-label="Trailer door with metal steps"></div>
  <div class="product-name">Product Name</div>
  <p class="product-text">Sed ut perspiciatis unde omnis iste natus error sit voluptatem ac cusantium dolorem</p>
  <div class="product-btn">View Details</div>
</article>
<article class="abs product-card" style="left:360px">
  <div class="product-img" style="background:linear-gradient(160deg,#4f6a3c,#1c5fb0 50%,#7a5a40)" role="img" aria-label="Blue portable toilet in a vineyard"></div>
  <div class="product-name">Product Name</div>
  <p class="product-text">Sed ut perspiciatis unde omnis iste natus error sit voluptatem ac cusantium dolorem</p>
  <div class="product-btn">View Details</div>
</article>
<article class="abs product-card" style="left:609px">
  <div class="product-img" style="background:linear-gradient(160deg,#3d3a40,#ee6a25 50%,#6c6560)" role="img" aria-label="Orange portable toilet on a trailer"></div>
  <div class="product-name">Product Name</div>
  <p class="product-text">Sed ut perspiciatis unde omnis iste natus error sit voluptatem ac cusantium dolorem</p>
  <div class="product-btn">View Details</div>
</article>
<article class="abs product-card" style="left:857px">
  <div class="product-img" style="background:linear-gradient(90deg,#e2c020,#d8dde2 50%,#e2c020)" role="img" aria-label="White portable toilet in front of a yellow container"></div>
  <div class="product-name">Product Name</div>
  <p class="product-text">Sed ut perspiciatis unde omnis iste natus error sit voluptatem ac cusantium dolorem</p>
  <div class="product-btn">View Details</div>
</article>

<section>
  <div class="abs contact-photo" role="img" aria-label="Man working on a laptop in a bright room"></div>
  <h2 class="abs quote-title">Contact Us For A Quote</h2>
  <div class="abs rule" style="left:474px;top:2161px"></div>

  <div class="abs field" style="left:470px;top:2209px;width:318px">Name :</div>
  <div class="abs field" style="left:804px;top:2209px;width:317px">Email :</div>
  <div class="abs field" style="left:470px;top:2269px;width:318px">Phone :</div>
  <div class="abs field select" style="left:804px;top:2269px;width:317px">Type of Event? :</div>
  <div class="abs field select" style="left:470px;top:2327px;width:318px">How Many People? :</div>
  <div class="abs field" style="left:804px;top:2327px;width:317px">When Do You Need It</div>
  <div class="abs field" style="left:470px;top:2384px;width:651px">Type of Product Your Interestend In?</div>
  <div class="abs field select" style="left:470px;top:2442px;width:318px">For How Long? :</div>
  <div class="abs field" style="left:804px;top:2442px;width:317px">Where? :</div>
  <div class="abs submit">Submit</div>
</section>

<footer class="abs footer">
  <div class="abs footer-brand">Tidewell Comforts</div>
  <nav class="footer-nav">
    <a style="left:396px">HOME</a>
    <a style="left:508px">EVENT</a>
    <a style="left:633px">PRODUCT</a>
    <a style="left:779px">CONTACT US</a>
  </nav>
  <span class="social" style="left:515px" aria-label="Email">
    <svg width="16" height="12" viewBox="0 0 16 12"><rect x="1" y="1" width="14" height="10" fill="none" stroke="#fff" stroke-width="1.5"/><polyline points="1,1 8,7 15,1" fill="none" stroke="#fff" stroke-width="1.5"/></svg>
  </span>
  <span class="social" style="left:557px" aria-label="Phone">
    <svg width="14" height="14" viewBox="0 0 14 14"><path d="M3 1 L5 1 L6 4 L4.5 5.5 Q6 8.5 8.5 9.5 L10 8 L13 9 L13 11 Q13 13 11 13 Q2 12 1 3 Q1 1 3 1 Z" fill="#fff"/></svg>
  </span>
  <span class="social" style="left:600px" aria-label="Location">
    <svg width="12" height="16" viewBox="0 0 12 16"><path d="M6 15 Q1 8 1 5.5 A5 5 0 0 1 11 5.5 Q11 8 6 15 Z" fill="#fff"/><circle cx="6" cy="5.5" r="1.8" fill="var(--black7)"/></svg>
  </span>
  <span class="social" style="left:643px" aria-label="Chat">
    <svg width="16" height="14" viewBox="0 0 16 14"><path d="M2 1 H14 Q15 1 15 2 V9 Q15 10 14 10 H6 L3 13 V10 H2 Q1 10 1 9 V2 Q1 1 2 1 Z" fill="#fff"/></svg>
  </span>
  <span class="social" style="left:686px" aria-label="Website">
    <svg width="16" height="16" viewBox="0 0 16 16"><circle cx="8" cy="8" r="6.5" fill="none" stroke="#fff" stroke-width="1.4"/><ellipse cx="8" cy="8" rx="3" ry="6.5" fill="none" stroke="#fff" stroke-width="1.2"/><line x1="1.5" y1="8" x2="14.5" y2="8" stroke="#fff" stroke-width="1.2"/></svg>
  </span>
  <div class="abs copy">© Copyright 2022 Tidewell Comforts.All Rights Reserved</div>
</footer>

</body>
</html>
```